Counseling Practice Business Card

I need a professional looking business card incorporating my new logo that was just completed. Card needs to incorporate my name and title, description of my specialty, my address, my phone number, my fax number, my email and my website URL. I need to be able to choose design on/with different paper colors and textures.
I do not have a lot of business card ideas so I am open to anything but I want bold,sharp, clear card without additional designs other than my logo (see attached file info). I am open to different color backgrounds or paper colors including black. I do not like traditional brackets around area codes in phone number or dashes between numbers in phone number. Am open to other ways of presenting including periods between numbers as appropriate. I do not know enough to know what I like yet but I want card to coordinate and work together with my logo. My practice emphasizes natural mental health interventions so any use of color (with background paper color or the blue and green in my logo) that elicits nature is nice. In addition to black, any natural brown or wood looking background might be desirable also. Most of the offerings so far look very similar and boring.

Target Market(s)

Potential therapy clients and other professionals

Contact Information for Business Card

Card information:
Gerald M. Whitcombe, Ph.D.
Licensed Clinical Psychologist
Integrative Health Coach
4812 Marlowe Ridge Blvd SE
Suite 310
Ashbrook, GA 30412
(770) 415-2983 phone
(770) 581-4096 fax
drgeraldwhitcombe@quillmarsh.net
brightfernwellness.net

Font styles to use
Serif
Sans Serif
Other font styles liked:
• anything that you think looks crisp, clear and easily readable

Requirements
Must have
• Any color used should coordinate with my logo design (see attached files).
• Card should be printed horizontally so top and bottom are longest sides of rectangle.
• Background color or paper color should complement and highlight logo. Do not like a white background. black, grey, brown or any color my logo would blend well with.
Nice to have
• I would like designer to utilize color to highlight letters/name or phone-fax-web symbols.
• Bottom edge of card could be highlighted if appropriate to an idea.
Should not have
• I would NOT want the card to have a pure white background at all.
• No clear cards.
• Cards should be oriented with long sides on bottom and top, NOT sides. DO NOT LIKE THIS THIN TALL ORIENTATION.

```html
<!DOCTYPE html>
<html lang="en">
<head>
<meta charset="utf-8">
<title>Brightfern Wellness – Business Card</title>
<link rel="stylesheet" href="https://fonts.googleapis.com/css2?family=Roboto:wght@400;500&family=Roboto+Condensed:wght@700&display=swap">
<style>
  :root {
    --backdrop: #e8e4dd;
    --card-black: #121214;
    --brand-blue: #2a72b8;
    --brand-green: #0e6b36;
    --title-green: #1b8a45;
    --text-white: #ffffff;
    --url-grey: #c9ccd0;
  }
  html, body {
    margin: 0;
    width: 1200px;
    height: 960px;
    overflow: hidden;
    background: var(--backdrop);
    font-family: "Roboto", Arial, sans-serif;
  }
  .canvas { position: relative; width: 1200px; height: 960px; }
  .card {
    position: absolute;
    width: 598px;
    height: 343px;
    background: var(--card-black);
    overflow: hidden;
    box-shadow: 0 3px 6px rgba(0,0,0,0.35);
  }
  .card--front { left: 314px; top: 113px; }
  .card--back { left: 312px; top: 472px; }
  .card__swoosh { position: absolute; inset: 0; }

  .identity { position: absolute; left: 31px; top: 32px; }
  .identity__name {
    margin: 0;
    font-family: "Roboto Condensed", "Arial Narrow", sans-serif;
    font-weight: 700;
    font-size: 19px;
    color: var(--brand-blue);
    text-transform: uppercase;
  }
  .identity__title {
    margin: 4px 0 0;
    font-size: 14.5px;
    font-weight: 500;
    line-height: 19px;
    color: var(--title-green);
  }

  .brand-name {
    position: absolute;
    left: 0; right: 0;
    text-align: center;
    font-family: "Roboto", Arial, sans-serif;
    font-weight: 500;
    color: var(--brand-blue);
    white-space: nowrap;
  }
  .card--front .brand-name { top: 132px; font-size: 30px; left: -30px; }
  .card--back .brand-name { top: 144px; font-size: 42px; }

  .contact {
    position: absolute;
    right: 19px;
    top: 201px;
    margin: 0;
    padding: 0;
    list-style: none;
    text-align: right;
    color: var(--text-white);
    font-size: 13px;
  }
  .contact__item { height: 19px; display: flex; justify-content: flex-end; align-items: center; gap: 6px; }
  .contact__icon { width: 12px; height: 12px; fill: var(--text-white); }
  .address {
    position: absolute;
    right: 25px;
    top: 281px;
    margin: 0;
    font-style: normal;
    font-size: 14px;
    line-height: 18px;
    text-align: right;
    color: var(--text-white);
  }

  .url-band {
    position: absolute;
    left: 0; right: 0;
    top: 278px;
    height: 31px;
    background: var(--brand-green);
    color: var(--url-grey);
    font-size: 14px;
    letter-spacing: 3.6px;
    text-align: center;
    line-height: 31px;
  }
</style>
</head>
<body>
<main class="canvas">
  <section class="card card--front" aria-label="Card front">
    <svg class="card__swoosh" viewBox="0 0 598 343" width="598" height="343" aria-hidden="true">
      <path fill="var(--brand-green)" d="M0,232 C150,272 330,268 445,182 C523,122 570,58 594,0 L598,0 L598,343 L0,343 Z"/>
      <path fill="var(--brand-blue)" d="M0,248 C150,285 330,282 452,192 C530,134 575,62 598,2 L598,343 L0,343 Z"/>
    </svg>

    <div class="identity">
      <h1 class="identity__name">Gerald M. Whitcombe, Ph.D.</h1>
      <p class="identity__title">Licensed Clinical Psychologist<br>Integrative Health Coach</p>
    </div>

    <div class="brand-name">Brightfern Wellness</div>

    <ul class="contact">
      <li class="contact__item">(770) 415-2983
        <svg class="contact__icon" viewBox="0 0 24 24" aria-hidden="true"><path d="M6.6 10.8a15.1 15.1 0 0 0 6.6 6.6l2.2-2.2c.3-.3.7-.4 1-.2 1.1.4 2.3.6 3.6.6.6 0 1 .4 1 1V20c0 .6-.4 1-1 1A17 17 0 0 1 3 4c0-.6.4-1 1-1h3.5c.6 0 1 .4 1 1 0 1.3.2 2.5.6 3.6.1.3 0 .7-.2 1z"/></svg>
      </li>
      <li class="contact__item">(770) 581-4096
        <svg class="contact__icon" viewBox="0 0 24 24" aria-hidden="true"><path d="M6 3h12v5H6zM3 9h18a1 1 0 0 1 1 1v8h-4v3H6v-3H2v-8a1 1 0 0 1 1-1zm5 7v3h8v-3z"/></svg>
      </li>
      <li class="contact__item">drgeraldwhitcombe@quillmarsh.net
        <svg class="contact__icon" viewBox="0 0 24 24" aria-hidden="true"><path d="M2 5h20v14H2zm2 2v.5l8 5 8-5V7z"/></svg>
      </li>
      <li class="contact__item">www.brightfernwellness.net
        <svg class="contact__icon" viewBox="0 0 24 24" aria-hidden="true"><path d="M12 2a10 10 0 1 0 0 20 10 10 0 0 0 0-20zm-1 17.9A8 8 0 0 1 4.2 10L9 14.8v1.1a2 2 0 0 0 2 2zm6.9-2.5A2 2 0 0 0 16 16h-1v-3a1 1 0 0 0-1-1H8v-2h2a1 1 0 0 0 1-1V7h2a2 2 0 0 0 2-2v-.4a8 8 0 0 1 2.9 12.8z"/></svg>
      </li>
    </ul>

    <address class="address">4812 Marlowe Ridge Blvd SE<br>Suite 310 Ashbrook, GA 30412</address>
  </section>

  <section class="card card--back" aria-label="Card back">
    <div class="brand-name">Brightfern Wellness</div>
    <div class="url-band">www.brightfernwellness.net</div>
  </section>
</main>
</body>
</html>
```